Website Design for a holiday home letting busines

We require a redesign of our present website www.pinebrookstays.com. We want the website to stand out and look professional and clean to make holiday hunters want to book a caravan or lodge holiday with us. Our logo is red however we DO NOT want the website to be red. We want a natural colour scheme.

The final design should communicate that we are a professional company to book with.

On the home page we require;
Overview of company
Photo
Search box for holiday (check in)
Late Deals
Reviews
News

We would like the following pages designed; home page, available dates page, caravans page, content page.

The website should be responsive for smart phones. One website I do like is http://www.verdoliso.be/nl/

Target Market(s)

Families

Industry/Entity Type

Travel

Number of Pages Required

5+ page

Font styles to use
Serif

Requirements
Must have
• The project must be responsive for mobile phones and tablets.
• Ability to search for holiday home holidays
• We want a natural colour scheme.
Nice to have
• A style we like is http://www.verdoliso.be/nl/
Should not have
• Do not use red as a colour for the website. Our logo is red so this is the only time we want this used.

```html
<!DOCTYPE html>
<html lang="en">
<head>
<meta charset="utf-8">
<title>Pinebrook Stays – 2015 Holidays at Alderwick Holiday Park</title>
<link href="https://fonts.googleapis.com/css2?family=Open+Sans:wght@400;600;700&display=swap" rel="stylesheet">
<style>
:root{
  --blue:#1d6db4;
  --blue-dark:#155a96;
  --orange:#f0a020;
  --green:#7ab648;
  --ink:#333;
  --muted:#777;
  --footer:#232323;
  --footer-bar:#181818;
  --white:#fff;
}
*{box-sizing:border-box;margin:0;padding:0}
html,body{width:710px;height:1200px;overflow:hidden}
body{font-family:"Open Sans",Arial,sans-serif;color:var(--ink);background:#f4f4f4;font-size:8px;line-height:1.45;position:relative}
.site-header{height:62px;background:var(--white);position:relative}
.brand{position:absolute;left:44px;top:16px;display:flex;align-items:center;gap:6px;font-weight:700;font-size:17px;color:var(--blue-dark)}
.brand-mark{width:14px;height:14px;background:var(--blue-dark)}
.enquiry{position:absolute;right:130px;top:14px;display:flex;gap:6px;align-items:center}
.enquiry small{display:block;font-size:6.5px;color:var(--muted);letter-spacing:.5px}
.enquiry strong{font-size:11px;color:var(--blue-dark)}
.chat-btn{position:absolute;right:40px;top:12px;width:80px;height:34px;border-radius:5px;background:var(--blue);color:var(--white);padding:5px 8px;font-size:7px;line-height:1.2}
.chat-btn b{display:block;font-size:11px}
.hero{position:relative;height:88px;background:linear-gradient(180deg,#cfe2f2 0%,#e9f0f4 45%,#c9cfc4 75%,#8ea57c 100%)}
.main-nav{position:absolute;left:40px;right:40px;top:4px;height:22px;background:var(--white);display:flex;align-items:center;border-bottom:2px solid var(--blue)}
.main-nav a{font-size:6.5px;font-weight:600;color:var(--muted);text-decoration:none;padding:0 9px;height:100%;display:flex;align-items:center;letter-spacing:.3px}
.main-nav a.active{background:var(--blue);color:var(--white)}
.page{position:absolute;left:40px;top:150px;width:630px;height:845px;background:var(--white)}
.page-title{background:var(--blue);color:var(--white);font-size:13px;font-weight:700;padding:8px 14px}
.intro{display:flex;gap:14px;padding:14px}
.intro-photo{position:relative;width:290px;height:170px;background:linear-gradient(135deg,#a9c7de,#e6e2d6 55%,#9bb28a)}
.intro-photo p{position:absolute;left:0;right:0;bottom:0;background:rgba(29,109,180,.85);color:var(--white);font-size:6.5px;padding:5px 8px}
.plans{flex:1}
.plans h3{color:var(--blue);font-size:10px;margin-bottom:4px}
.plans ul{list-style:none;margin-bottom:12px}
.plans li{font-size:7px;color:var(--muted);padding-left:12px;position:relative;margin-bottom:3px}
.plans li svg{position:absolute;left:0;top:2px}
.copy{padding:0 14px;color:var(--muted);font-size:7px}
.copy h4{color:var(--ink);font-size:8px;margin:6px 0 2px}
.copy ul{padding-left:12px;margin-bottom:6px}
.homes{display:flex;gap:8px;padding:12px 14px 0}
.home{flex:1}
.home-photo{height:80px}
.home-name{background:var(--blue);color:var(--white);font-weight:700;font-size:8px;padding:4px 6px;height:30px;line-height:1.2}
.home-name span{display:block;font-weight:400;font-size:6.5px}
.sleeps{display:flex;gap:8px;padding:6px 14px}
.sleeps div{flex:1;display:flex;align-items:center;gap:4px;font-size:7px}
.sleeps b{display:inline-block;background:var(--blue);color:var(--white);font-size:7px;padding:1px 6px;border-radius:2px}
.sleeps i{font-style:normal;color:var(--blue);font-weight:700}
.availability{margin:10px 14px 0;background:var(--blue);padding:12px 10px}
.availability table{width:100%;border-collapse:separate;border-spacing:3px 5px}
.availability th{text-align:left;color:var(--white);font-weight:400;font-size:6.3px;width:150px;white-space:nowrap}
.availability td{background:var(--white);color:var(--blue-dark);font-size:5.5px;font-weight:700;text-align:center;height:22px;letter-spacing:.3px}
.availability td.price{background:var(--orange);color:var(--white)}
.note{display:flex;gap:6px;padding:12px 14px;font-size:7px;color:var(--muted)}
.site-footer{position:absolute;left:0;top:1005px;width:710px;height:165px;background:var(--footer);color:#bbb;display:flex;gap:30px;padding:18px 40px}
.site-footer h5{color:var(--white);font-size:12px;font-weight:600;margin-bottom:8px}
.site-footer p{font-size:6.5px;margin-bottom:8px}
.col{flex:1}
.field{height:18px;background:var(--white);margin-bottom:6px;font-size:6.5px;color:#999;padding:4px 6px}
.subscribe{display:inline-block;background:var(--green);color:var(--white);font-size:7px;font-weight:700;padding:5px 14px}
.contact-line{display:flex;align-items:center;gap:5px;font-size:7px;margin-bottom:4px}
.sitemap{display:grid;grid-template-columns:1fr 1fr;gap:4px 10px;font-size:7px}
.bottom-bar{position:absolute;left:0;top:1170px;width:710px;height:30px;background:var(--footer-bar);color:#999;font-size:6.5px;display:flex;align-items:center;justify-content:space-between;padding:0 40px}
.social{display:flex;gap:5px;align-items:center}
.social span{width:10px;height:10px;border-radius:50%;background:#666;display:inline-block}
</style>
</head>
<body>
<header class="site-header">
  <div class="brand"><span class="brand-mark"></span>Pinebrook Stays</div>
  <div class="enquiry">
    <svg width="14" height="14" viewBox="0 0 24 24"><path fill="#1d6db4" d="M6.6 10.8a15 15 0 0 0 6.6 6.6l2.2-2.2c.3-.3.7-.4 1-.2 1.1.4 2.3.6 3.6.6.6 0 1 .4 1 1V20c0 .6-.4 1-1 1A17 17 0 0 1 3 4c0-.6.4-1 1-1h3.5c.6 0 1 .4 1 1 0 1.3.2 2.5.6 3.6.1.3 0 .7-.2 1z"/></svg>
    <div><small>GENERAL ENQUIRY</small><strong>0800 555 0142</strong></div>
  </div>
  <div class="chat-btn"><b>Questions?</b>Live Chat</div>
</header>

<div class="hero" role="img" aria-label="Caravans in a green holiday park under a blue sky">
  <nav class="main-nav">
    <a class="active">HOME</a><a>NEWS</a><a>REVIEWS</a><a>CARAVANS &amp; LODGES</a><a>PAYMENT PLANS</a><a>ALDERWICK PARK</a><a>LATE DEALS</a><a>CONTACT US</a>
  </nav>
</div>

<main class="page">
  <h1 class="page-title">2015 Caravan and Lodge Holidays at Alderwick Holiday Park</h1>
  <section class="intro">
    <div class="intro-photo" role="img" aria-label="Family relaxing on the decking of a holiday caravan">
      <p>Book your holiday for 2015 holidays at Alderwick Holiday Park and secure your 2015 dates before they are gone.</p>
    </div>
    <div class="plans">
      <h3>Weekly or Monthly Regular Payments</h3>
      <ul>
        <li><svg width="8" height="8" viewBox="0 0 10 10"><path d="M1 5l3 3 5-6" stroke="#7ab648" stroke-width="2" fill="none"/></svg>Available for holidays more than 3 months away.</li>
        <li><svg width="8" height="8" viewBox="0 0 10 10"><path d="M1 5l3 3 5-6" stroke="#7ab648" stroke-width="2" fill="none"/></svg>No deposit required to book.</li>
        <li><svg width="8" height="8" viewBox="0 0 10 10"><path d="M1 5l3 3 5-6" stroke="#7ab648" stroke-width="2" fill="none"/></svg>Choose either Weekly or Monthly Payments by Direct Debit.</li>
        <li><svg width="8" height="8" viewBox="0 0 10 10"><path d="M1 5l3 3 5-6" stroke="#7ab648" stroke-width="2" fill="none"/></svg>YOU select when you want payments to come out of your bank.</li>
        <li><svg width="8" height="8" viewBox="0 0 10 10"><path d="M1 5l3 3 5-6" stroke="#7ab648" stroke-width="2" fill="none"/></svg>Payments include refundable £50 bond.</li>
      </ul>
      <h3>Weekly or Monthly Regular Payments</h3>
      <ul>
        <li><svg width="8" height="8" viewBox="0 0 10 10"><path d="M1 5l3 3 5-6" stroke="#7ab648" stroke-width="2" fill="none"/></svg>Pay a £50 non-refundable deposit booking fee.</li>
        <li><svg width="8" height="8" viewBox="0 0 10 10"><path d="M1 5l3 3 5-6" stroke="#7ab648" stroke-width="2" fill="none"/></svg>Balance due 8 weeks before booking.</li>
        <li><svg width="8" height="8" viewBox="0 0 10 10"><path d="M1 5l3 3 5-6" stroke="#7ab648" stroke-width="2" fill="none"/></svg>Payments made either by Bank Transfer, secure online payment or over the telephone.</li>
      </ul>
    </div>
  </section>

  <section class="copy">
    <p>Please note that all bookings are subject to our booking terms and conditions. Our prices do not include leisure passes which are required to use the park facilities, entertainment, bars, swimming and kids activities. These can be purchased from the reception on arrival.</p>
    <h4>Please note:</h4>
    <ul>
      <li>We do not allow pets in our caravans.</li>
      <li>Alderwick Holiday Park does not allow single sex groups.</li>
    </ul>
    <p>Our prices below show 3 or 4 nights. If you are wanting a price for 7 nights please click on the price and the next page gives you an update to select 7 nights from a drop down.</p>
  </section>

  <section class="homes">
    <div class="home"><div class="home-photo" role="img" aria-label="Luxury lodge exterior" style="background:linear-gradient(135deg,#b8cfe0,#d9d4c6 60%,#8ea57c)"></div><div class="home-name">The Hawthorn<span>(Luxury Lodge)</span></div></div>
    <div class="home"><div class="home-photo" role="img" aria-label="Platinum caravan lounge interior" style="background:linear-gradient(135deg,#e4d9c6,#c7b79b 60%,#9c8a6d)"></div><div class="home-name">The Linden<span>(Platinum)</span></div></div>
    <div class="home"><div class="home-photo" role="img" aria-label="Prestige caravan living area" style="background:linear-gradient(135deg,#e9e2d4,#cbbfa8 60%,#8f7f66)"></div><div class="home-name">The Rowan<span>(Prestige)</span></div></div>
    <div class="home"><div class="home-photo" role="img" aria-label="Deluxe caravan lounge interior" style="background:linear-gradient(135deg,#e7ddcc,#b9a58a 60%,#7d6a52)"></div><div class="home-name">The Alder<span>(Deluxe Plus)</span></div></div>
  </section>
  <div class="sleeps">
    <div>Sleeps <b>6</b><i>›</i></div><div>Sleeps <b>6</b><i>›</i></div><div>Sleeps <b>6</b><i>›</i></div><div>Sleeps <b>6</b><i>›</i></div>
  </div>

  <section class="availability">
    <table>
      <tr><th>Fri 28 August – Mon 31 August 2015</th><td>BOOKED</td><td>BOOKED</td><td>BOOKED</td><td>BOOKED</td><td>BOOKED</td><td>BOOKED</td><td>BOOKED</td><td>BOOKED</td></tr>
      <tr><th>Mon 31 August – Fri 4 September 2015</th><td>BOOKED</td><td>BOOKED</td><td>BOOKED</td><td>BOOKED</td><td>BOOKED</td><td>BOOKED</td><td>BOOKED</td><td>BOOKED</td></tr>
      <tr><th>Fri 4 September – Mon 7 September 2015</th><td>BOOKED</td><td>BOOKED</td><td class="price">£295.00</td><td>BOOKED</td><td>BOOKED</td><td>BOOKED</td><td>BOOKED</td><td>BOOKED</td></tr>
      <tr><th>Mon 7 September – Fri 11 September 2015</th><td>BOOKED</td><td>BOOKED</td><td>BOOKED</td><td>BOOKED</td><td class="price">£275.00</td><td>BOOKED</td><td>BOOKED</td><td>BOOKED</td></tr>
      <tr><th>Fri 11 September – Mon 14 September 2015</th><td>BOOKED</td><td>BOOKED</td><td>BOOKED</td><td>BOOKED</td><td>BOOKED</td><td>BOOKED</td><td>BOOKED</td><td>BOOKED</td></tr>
      <tr><th>Mon 14 September – Fri 18 September 2015</th><td>BOOKED</td><td>BOOKED</td><td>BOOKED</td><td class="price">£265.00</td><td>BOOKED</td><td>BOOKED</td><td>BOOKED</td><td>BOOKED</td></tr>
      <tr><th>Fri 18 September – Mon 21 September 2015</th><td>BOOKED</td><td class="price">£245.00</td><td>BOOKED</td><td>BOOKED</td><td>BOOKED</td><td>BOOKED</td><td>BOOKED</td><td>BOOKED</td></tr>
      <tr><th>Mon 21 September – Fri 25 September 2015</th><td>BOOKED</td><td>BOOKED</td><td>BOOKED</td><td>BOOKED</td><td>BOOKED</td><td>BOOKED</td><td class="price">£235.00</td><td>BOOKED</td></tr>
    </table>
  </section>
  <p class="note">
    <svg width="9" height="9" viewBox="0 0 10 10"><path d="M1 5l3 3 5-6" stroke="#7ab648" stroke-width="2" fill="none"/></svg>
    Dates with a grey background indicated out of season. Holidays during these dates are advertised as quiet breaks. Please note that the pool facilities and complex are closed during this time.
  </p>
</main>

<footer class="site-footer">
  <div class="col">
    <h5>NEWSLETTER SIGNUP</h5>
    <p>Subscribe to our newsletter for the latest late deals and park news.</p>
    <div class="field">Enter Your Name</div>
    <div class="field">Enter Your Email</div>
    <span class="subscribe">SUBSCRIBE</span>
  </div>
  <div class="col">
    <h5>CONTACT INFORMATION</h5>
    <p>Contact our friendly team for bookings, availability and any questions about your caravan or lodge holiday at the park.</p>
    <div class="contact-line"><svg width="8" height="8" viewBox="0 0 24 24"><path fill="#bbb" d="M6.6 10.8a15 15 0 0 0 6.6 6.6l2.2-2.2c.3-.3.7-.4 1-.2 1.1.4 2.3.6 3.6.6.6 0 1 .4 1 1V20c0 .6-.4 1-1 1A17 17 0 0 1 3 4c0-.6.4-1 1-1h3.5c.6 0 1 .4 1 1 0 1.3.2 2.5.6 3.6.1.3 0 .7-.2 1z"/></svg>0800 555 0142</div>
    <div class="contact-line"><svg width="8" height="8" viewBox="0 0 24 24"><path fill="none" stroke="#bbb" stroke-width="2" d="M3 5h18v14H3zM3 5l9 8 9-8"/></svg>hello@pinebrookstays.com</div>
  </div>
  <div class="col">
    <h5>SITEMAP</h5>
    <div class="sitemap">
      <span>About Us</span><span>Reviews</span><span>News</span><span>Privacy Policy</span><span>Blogs</span><span>Booking Terms</span><span>2015 Holidays</span><span>News</span><span>Late Deals</span><span>Site Search</span><span>Local Areas</span>
    </div>
  </div>
</footer>
<div class="bottom-bar">
  <span>Pinebrook Stays 2015 – All Rights Reserved</span>
  <div class="social">Social Icons <span></span><span></span><span></span><span></span><span></span></div>
</div>
</body>
</html>
```